RW Framewell Inc Business cards

We need business cards using our existing logo but slightly modified. Right now the logo says RW Loadbearing Masonry. We want to keep the RW part of the design, but replace the Structural Concrete portion with "FRAMEWELL". Please see the attached file.
Ideally this would be a blank template so we can add Different Names, titles, and phone numbers later.
On the one side we want only the logo and on the other side the detail. I'm attaching an example for you to see.
Please reach out with any other questions. Our address and other details will be given out once we find a design we like.

Target Market(s)

Construction Industry

```html
<!DOCTYPE html>
<html lang="en">
<head>
<meta charset="utf-8">
<title>RW Framewell Inc – Business Cards</title>
<link rel="stylesheet" href="https://fonts.googleapis.com/css2?family=Archivo+Black&family=Roboto:wght@400&display=swap">
<style>
  :root {
    --page-bg: #b9b9b9;
    --brand-blue: #1a76bf;
    --card-white: #ffffff;
    --text-grey: #5f6063;
    --rule-grey: #9a9a9a;
  }
  * { margin: 0; padding: 0; box-sizing: border-box; }
  html, body {
    width: 1200px; height: 1200px; overflow: hidden;
    background: var(--page-bg);
  }
  .sheet { position: relative; width: 1200px; height: 1200px; }
  .card {
    position: absolute; top: 304px;
    width: 368px; height: 592px;
    border-radius: 20px;
  }
  .card-front { left: 219px; background: var(--brand-blue); }
  .card-back { left: 617px; background: var(--card-white); }

  .wordmark {
    position: absolute; left: 0; right: 0;
    text-align: center;
    font-family: "Archivo Black", sans-serif;
    letter-spacing: 1px;
    line-height: 1;
  }
  .wordmark .initials { display: block; font-size: 96px; }
  .wordmark .name { display: block; font-size: 30px; margin-top: 10px; }
  .card-front .wordmark { top: 236px; color: var(--card-white); }
  .card-back .wordmark { top: 118px; color: var(--brand-blue); }

  .details {
    position: absolute; left: 0; right: 0; top: 394px;
    text-align: center;
    font-family: "Roboto", sans-serif;
    color: var(--text-grey);
  }
  .person-name {
    font-family: "Archivo Black", sans-serif;
    font-size: 22px; color: var(--brand-blue);
    letter-spacing: 0.5px; line-height: 26px;
  }
  .person-title { font-size: 17px; line-height: 22px; }
  .icon-row {
    display: flex; align-items: center; justify-content: center;
    gap: 4px; margin-top: 13px; height: 26px;
  }
  .icon-row .rule { width: 52px; height: 1px; background: var(--rule-grey); margin: 0 2px; }
  .icon {
    width: 25px; height: 25px; border-radius: 3px;
    background: var(--brand-blue);
    display: flex; align-items: center; justify-content: center;
  }
  .contact-lines { margin-top: 12px; font-size: 17px; line-height: 22px; }
</style>
</head>
<body>
<main class="sheet">
  <section class="card card-front" aria-label="Card front">
    <div class="wordmark">
      <span class="initials">RW</span>
      <span class="name">FRAMEWELL</span>
    </div>
  </section>

  <section class="card card-back" aria-label="Card back">
    <div class="wordmark">
      <span class="initials">RW</span>
      <span class="name">FRAMEWELL</span>
    </div>

    <div class="details">
      <p class="person-name">DANIEL HARWICK</p>
      <p class="person-title">Managing Director</p>
      <div class="icon-row">
        <span class="rule"></span>
        <span class="icon" aria-label="Phone">
          <svg width="16" height="16" viewBox="0 0 16 16" fill="#fff">
            <path d="M2 6c0-2 3-3 6-3s6 1 6 3v1h-3V6H5v1H2z"/>
            <rect x="4" y="8" width="8" height="5" rx="1"/>
          </svg>
        </span>
        <span class="icon" aria-label="Email">
          <svg width="16" height="16" viewBox="0 0 16 16" fill="none" stroke="#fff" stroke-width="1.2">
            <rect x="2" y="4" width="12" height="8"/>
            <path d="M2 4l6 5 6-5M2 12l4.5-4M14 12l-4.5-4"/>
          </svg>
        </span>
        <span class="icon" aria-label="Website">
          <svg width="16" height="16" viewBox="0 0 16 16" fill="none" stroke="#fff" stroke-width="1.2">
            <circle cx="8" cy="8" r="6" fill="#fff"/>
            <path d="M8 2v12M2 8h12M4 4c2 1.5 6 1.5 8 0M4 12c2-1.5 6-1.5 8 0" stroke="#1a76bf"/>
          </svg>
        </span>
        <span class="rule"></span>
      </div>
      <div class="contact-lines">
        <p>044-555 010 234</p>
        <p>info@framewellmail.com</p>
        <p>www.framewellsite.com</p>
      </div>
    </div>
  </section>
</main>
</body>
</html>
```